Tolvin Audio™ – Water Resistant Bluetooth Speakers

Looking for someone who is very experienced with retail product packaging.
We currently have a blank retail box with product window area and we need a design created to print on that box.
The design will need to be crisp, clean and appealing to consumers as well as have all of the proper retail wording, requirements etc.
The product is a bluetooth speaker/speakerphone that goes anywhere, even the shower!
We need this created asap.
Updates

Project Deadline Extended
Reason: We have quite a few really good designs, we want to give everyone a chance to work with our team to get text and layouts updated how we want them and then we will make a final decision.

Target Market(s)

Consumer Electronics Shoppers

Industry/Entity Type

Retail

Requirements
Must have
• Design must stand out to consumers and clearly display what makes this product unique but remain clean and simple, think Quarrow packaging.
Printed areas must include all 4 sides and top of box.
UPC area on the back of box.
See http://www.brendalcraftworks.com/product/tolvin-audio-water-resistant-bluetooth-speakers/ for product details and descriptions.
Nice to have
• No need for a logo, can just be font based, if you make a logo great, but not needed.

```html
<!DOCTYPE html>
<html lang="en">
<head>
<meta charset="utf-8">
<title>Tolvin Audio™ – Water Resistant Bluetooth Speakers Packaging</title>
<link rel="stylesheet" href="https://fonts.googleapis.com/css2?family=Roboto+Condensed:wght@400;700&family=Roboto:wght@400;700;900&display=swap">
<style>
  :root {
    --bg: #ffffff;
    --ink: #1e1e1e;
    --grey-text: #9a9a9a;
    --pale-grey: #d4d4d4;
    --panel: #f2f2f2;
    --orange: #ec5a12;
    --orange-deep: #e0480c;
    --amber: #f6b33a;
    --yellow: #f9c84a;
    --side-light: #6e5c2c;
    --side-dark: #3f341a;
    --window-dark: #555555;
    --window-light: #cfcfcf;
  }
  * { margin: 0; padding: 0; box-sizing: border-box; }
  html, body { width: 1200px; height: 775px; overflow: hidden; background: var(--bg); }
  body { font-family: "Roboto", Arial, sans-serif; color: var(--ink); position: relative; }

  .brand-header { position: absolute; left: 135px; top: 62px; }
  .brand-header__name { font-weight: 900; font-size: 23px; letter-spacing: 0.3px; }
  .brand-header__name sup { font-size: 11px; font-weight: 700; }
  .brand-header__tagline { font-weight: 700; font-size: 12px; color: var(--pale-grey); margin-top: 3px; letter-spacing: 0.3px; }
  .brand-header__sub { font-weight: 700; font-size: 9.5px; color: var(--grey-text); margin-top: 6px; line-height: 1.3; }

  /* Flat box net: top panel, main face, side panel */
  .box { position: absolute; top: 205px; width: 450px; height: 330px; filter: drop-shadow(0 16px 22px rgba(0,0,0,0.14)); }
  .box--back { left: 120px; }
  .box--front { left: 630px; }

  .box__top {
    position: absolute; top: 0; width: 380px; height: 60px;
    background: linear-gradient(90deg, var(--amber), var(--yellow) 55%, #fbe0a0);
  }
  .box--back .box__top { left: 70px; }
  .box--front .box__top { left: 0; }

  .box__side {
    position: absolute; top: 60px; width: 70px; height: 270px; overflow: hidden;
    background: linear-gradient(90deg, var(--side-dark), var(--side-light));
  }
  .box--back .box__side { left: 0; background: linear-gradient(90deg, var(--side-light), var(--side-dark)); }
  .box--front .box__side { left: 380px; }
  .side__brand {
    position: absolute; top: 14px; left: 10px; font-family: "Roboto Condensed", Arial, sans-serif;
    font-weight: 700; font-size: 7px; color: var(--orange); line-height: 1.3;
  }
  .side__badge { position: absolute; bottom: 60px; width: 14px; height: 22px; background: var(--orange); border-radius: 2px; }
  .box--back .side__badge { left: 12px; }
  .box--front .side__badge { right: 12px; }
  .side__base { position: absolute; left: 0; right: 0; bottom: 0; height: 40px; background: rgba(0,0,0,0.22); }

  .panel { position: absolute; top: 60px; width: 380px; height: 270px; background: var(--panel); overflow: hidden; }
  .box--back .panel { left: 70px; }
  .box--front .panel { left: 0; }

  .panel__footer {
    position: absolute; left: 0; right: 0; bottom: 0; height: 40px;
    background: linear-gradient(180deg, var(--orange), var(--orange-deep));
    color: #fff; font-weight: 700; font-size: 10px; text-align: center; line-height: 44px; letter-spacing: 0.4px;
  }
  .panel__footer sup { font-size: 6px; }

  .back-strip { position: absolute; top: 16px; left: 40px; right: 0; display: flex; align-items: center; }
  .back-strip__label { font-family: "Roboto Condensed", Arial, sans-serif; font-size: 7.5px; color: var(--grey-text); line-height: 1.2; width: 96px; }
  .back-strip__bar { width: 40px; height: 13px; background: var(--amber); margin-right: 4px; }
  .back-strip__tag { flex: 1; height: 15px; background: var(--orange); color: #fff; font-family: "Roboto Condensed", Arial, sans-serif; font-weight: 700; font-size: 8.5px; line-height: 15px; padding-left: 7px; white-space: nowrap; }

  .feature-list { position: absolute; top: 50px; left: 55px; width: 195px; list-style: none; font-family: "Roboto Condensed", Arial, sans-serif; font-weight: 700; font-size: 9.5px; color: var(--orange); line-height: 1.22; }
  .feature-list li { position: relative; padding-left: 11px; }
  .feature-list li::before { content: ""; position: absolute; left: 0; top: 3.5px; width: 5px; height: 5px; border-radius: 50%; background: var(--orange); }

  .spec-list { position: absolute; top: 130px; left: 65px; list-style: none; font-family: "Roboto Condensed", Arial, sans-serif; font-size: 5.5px; color: var(--orange); line-height: 1.3; }
  .spec-list li::before { content: "- "; }

  .cert-marks { position: absolute; top: 92px; left: 265px; display: flex; gap: 4px; }
  .cert-marks span { width: 10px; height: 10px; border-radius: 50%; border: 1.5px solid var(--orange); }
  .cert-marks span:last-child { background: var(--orange); }

  .upc-area { position: absolute; top: 118px; left: 250px; width: 100px; height: 66px; background: #fff; border-radius: 6px; border: 1px solid #e6e6e6; display: flex; align-items: center; justify-content: center; font-size: 10px; color: var(--pale-grey); font-weight: 700; }

  .front-title { position: absolute; top: 18px; left: 14px; font-family: "Roboto Condensed", Arial, sans-serif; font-weight: 700; font-size: 14px; color: var(--orange); white-space: nowrap; }
  .front-sub { position: absolute; top: 37px; left: 14px; font-family: "Roboto Condensed", Arial, sans-serif; font-size: 7.5px; color: var(--grey-text); line-height: 1.2; }
  .product-window { position: absolute; top: 62px; left: 98px; width: 190px; height: 150px; border-radius: 10px; border: 3px solid #fff; box-shadow: 0 0 0 1px #ccc; background: linear-gradient(135deg, var(--window-light) 0%, #9a9a9a 45%, var(--window-dark) 46%, #6e6e6e 100%); }
  .partner-mark { position: absolute; top: 196px; left: 14px; display: flex; align-items: center; gap: 4px; font-weight: 700; font-size: 8px; color: var(--ink); }
  .partner-mark__dot { width: 7px; height: 7px; border-radius: 50%; background: var(--ink); }
</style>
</head>
<body>
  <header class="brand-header">
    <h1 class="brand-header__name">TOLVIN AUDIO<sup>™</sup></h1>
    <p class="brand-header__tagline">WATER RESISTANT BLUETOOTH SPEAKERS</p>
    <p class="brand-header__sub">PORTABLE AUDIO SYSTEM<br>WITH BLUETOOTH</p>
  </header>

  <section class="box box--back" aria-label="Back and left side of box">
    <div class="box__top" aria-label="Top of box"></div>
    <div class="box__side" aria-label="Left side of box">
      <p class="side__brand">TOLVIN<br>AUDIO</p>
      <span class="side__badge"></span>
      <span class="side__base"></span>
    </div>
    <div class="panel">
      <div class="back-strip">
        <p class="back-strip__label">PORTABLE AUDIO SYSTEM<br>WITH BLUETOOTH</p>
        <div class="back-strip__bar"></div>
        <p class="back-strip__tag">WATER RESISTANT BLUETOOTH SPEAKERS</p>
      </div>
      <ul class="feature-list">
        <li>Bass boost (passive subwoofer)</li>
        <li>Power by detachable lithium-ion rechargeable battery of 18650, type, 3.7 V, 1800 mA/h</li>
        <li>Charging via mini-USB</li>
        <li>Color: black</li>
      </ul>
      <div class="cert-marks" aria-label="Certification marks"><span></span><span></span><span></span><span></span><span></span></div>
      <ul class="spec-list">
        <li>LED display</li>
        <li>High sensitivity FM tuner, wide band</li>
        <li>40 FM station preset memory</li>
        <li>Audio playback from micro SD card</li>
        <li>Format support: MP3, WMA</li>
        <li>Audio playback from paired devices</li>
        <li>Wireless range up to 10 meters</li>
        <li>Built-in clock</li>
        <li>Aux in</li>
        <li>Headphones jack</li>
        <li>Stereo sound</li>
        <li>Output power 2 x 3 W</li>
      </ul>
      <div class="upc-area">UPC AREA</div>
      <footer class="panel__footer">TOLVIN AUDIO<sup>™</sup></footer>
    </div>
  </section>

  <section class="box box--front" aria-label="Front and right side of box">
    <div class="box__top" aria-label="Top of box"></div>
    <div class="panel">
      <h2 class="front-title">WATER RESISTANT BLUETOOTH SPEAKERS</h2>
      <p class="front-sub">PORTABLE AUDIO SYSTEM<br>WITH BLUETOOTH</p>
      <div class="product-window" role="img" aria-label="Clear window showing the speaker inside"></div>
      <div class="partner-mark"><span class="partner-mark__dot"></span>Linkwave</div>
      <footer class="panel__footer">TOLVIN AUDIO<sup>™</sup></footer>
    </div>
    <div class="box__side" aria-label="Right side of box">
      <p class="side__brand">TOLVIN<br>AUDIO</p>
      <span class="side__badge"></span>
      <span class="side__base"></span>
    </div>
  </section>
</body>
</html>
```